Web Developer Needs a Business Card Design

I need a personal business card design that represents me as a web developer for potential employers. I would like the background to be a dark color on the front for contrast with my logo and name. The back will have all my information along with a smaller version of the logo. I want something with a modern look and feel, not too conservative. This will be used for potential employers and freelance work.

Industry/Entity Type

Business

Contact Information for Business Card

Front should have my logo and name. The back should have all my personal information which would include: name: Tom Varulek, phone: 570-614-3098, email: tomvarulek@quillbox.net, website url: www.tomvarulek.net, logo, web developer.

Font styles to use
Sans Serif

Requirements
Must have
• Must include my logo. The color palette base color will be the logo color.

```html
<!DOCTYPE html>
<html lang="en">
<head>
<meta charset="utf-8">
<title>Tom Varulek – Business Card</title>
<link rel="stylesheet" href="https://fonts.googleapis.com/css2?family=Questrial&family=Roboto:wght@300;400&display=swap">
<style>
  :root {
    --bg: #8a8c8b;
    --card-dark: #241c1b;
    --teal: #45c9a6;
    --text-light: #d9d6d3;
    --text-soft: #bdb8b4;
    --photo-dark: #2a2221;
    --photo-mid: #3a3130;
    --photo-grey: #4a4847;
  }
  * { box-sizing: border-box; margin: 0; padding: 0; }
  html, body { width: 1200px; height: 900px; overflow: hidden; }
  body {
    background: var(--bg);
    position: relative;
    font-family: "Questrial", sans-serif;
  }
  .card {
    position: absolute;
    left: 320px;
    width: 560px;
    height: 320px;
    overflow: hidden;
  }
  .card--info { top: 110px; background: var(--card-dark); }
  .card--name { top: 480px; }

  .mark {
    position: absolute;
    left: 0; right: 0;
    display: flex;
    align-items: center;
    justify-content: center;
    gap: 12px;
    color: var(--teal);
    font-family: "Questrial", sans-serif;
  }
  .mark__ring {
    border: 4px solid var(--teal);
    border-radius: 50%;
  }
  .card--info .mark { top: 60px; font-size: 38px; }
  .card--info .mark__ring { width: 40px; height: 40px; }
  .card--name .mark { top: 84px; font-size: 30px; }
  .card--name .mark__ring { width: 32px; height: 32px; }

  .contacts {
    position: absolute;
    top: 206px;
    left: 0; right: 0;
    display: flex;
    flex-direction: column;
    align-items: center;
    gap: 8px;
    color: var(--text-light);
    font-size: 15px;
  }
  .contacts__row { display: flex; gap: 16px; }
  .contact { display: flex; align-items: center; gap: 5px; }
  .contact svg { width: 18px; height: 18px; flex: none; }

  .photo-fill {
    position: absolute;
    inset: 0;
    background:
      radial-gradient(ellipse at 50% 95%, var(--photo-dark) 0%, transparent 35%),
      linear-gradient(90deg, var(--photo-grey) 0%, var(--photo-mid) 20%, var(--photo-dark) 50%, var(--photo-mid) 85%, var(--photo-grey) 100%);
  }
  .identity {
    position: absolute;
    left: 0; right: 0;
    text-align: center;
    font-family: "Roboto", sans-serif;
  }
  .identity__name {
    top: 190px;
    font-size: 29px;
    font-weight: 300;
    letter-spacing: 2px;
    color: var(--text-light);
  }
  .identity__title {
    top: 238px;
    font-size: 16px;
    font-weight: 300;
    letter-spacing: 1px;
    color: var(--text-soft);
  }
</style>
</head>
<body>

<section class="card card--info">
  <div class="mark"><span class="mark__ring"></span><span>varulek</span></div>

  <div class="contacts">
    <div class="contacts__row">
      <span class="contact">
        <svg viewBox="0 0 18 18" aria-hidden="true"><circle cx="9" cy="9" r="8" fill="none" stroke="var(--teal)" stroke-width="1.6"/><path d="M6 5.5c0 4 2.5 6.5 6.5 7l.8-1.6-1.8-1-1 .9C9 10.2 7.8 9 7.4 7.5l.9-1-1-1.8z" fill="var(--teal)"/></svg>
        570-614-3098
      </span>
      <span class="contact">
        <svg viewBox="0 0 18 18" aria-hidden="true"><circle cx="9" cy="9" r="8" fill="none" stroke="var(--teal)" stroke-width="1.6"/><rect x="4.5" y="6" width="9" height="6" rx="1" fill="var(--teal)"/></svg>
        tomvarulek@quillbox.net
      </span>
    </div>
    <div class="contacts__row">
      <span class="contact">
        <svg viewBox="0 0 18 18" aria-hidden="true"><circle cx="9" cy="9" r="8" fill="var(--teal)"/><path d="M1.5 9h15M9 1.5c-3 3-3 12 0 15M9 1.5c3 3 3 12 0 15" fill="none" stroke="var(--card-dark)" stroke-width="1.2"/></svg>
        www.tomvarulek.net
      </span>
      <span class="contact">
        <svg viewBox="0 0 18 18" aria-hidden="true"><circle cx="9" cy="9" r="8" fill="none" stroke="var(--teal)" stroke-width="1.6"/></svg>
        @tomvarulek.net
      </span>
    </div>
    <div class="contacts__row">
      <span class="contact">
        <svg viewBox="0 0 18 18" aria-hidden="true"><circle cx="9" cy="9" r="8" fill="none" stroke="var(--teal)" stroke-width="1.6"/></svg>
        tomvarulek.net
      </span>
      <span class="contact">
        <svg viewBox="0 0 18 18" aria-hidden="true"><circle cx="9" cy="9" r="8" fill="none" stroke="var(--teal)" stroke-width="1.6"/></svg>
        tomvarulek.net
      </span>
    </div>
  </div>
</section>

<section class="card card--name">
  <div class="photo-fill" role="img" aria-label="Dark top-down photo of a desk with a laptop, keyboard, notebook and a cup of coffee"></div>
  <div class="mark"><span class="mark__ring"></span><span>varulek</span></div>
  <p class="identity identity__name">TOM VARULEK</p>
  <p class="identity identity__title">Front-End Developer</p>
</section>

</body>
</html>
```